FinTech company looking to revamp and expand client-facing interface for our financial models

Pellworth Engines currently has a very simple website that allows clients to interact with our financial models. We are looking to completely redesign the current site and add several extra pages to provide extra functionality. We want the design to have a modern, slick feel, that will work on both a desktop or a tablet. It should be straightforward for clients to move between different pages at any time, and clear from the layout how to interact with the more advanced features. We have included screenshots of existing pages in the attached design brief, as well as sketches of the functionality required by the new pages, but can't provide a direct link to the current site.
Target Market(s)
Professional investors that will be paying to access the interface
Industry/Entity Type
Finance
Number of Pages Required
4 page
Colors
Designer to choose colors to be used in the design.
Look and feel
Each slider illustrates characteristics of the customer's brand and the style your logo design should communicate.

```html
<!DOCTYPE html>
<html lang="en">
<head>
<meta charset="utf-8">
<title>Pellworth Engines – Model Interface</title>
<link href="https://fonts.googleapis.com/css2?family=Poppins:wght@400;500;600;800&display=swap" rel="stylesheet">
<style>
  :root {
    --stage: #17273c;
    --white: #ffffff;
    --ink: #2b2f45;
    --text: #444a5c;
    --muted: #9aa0ad;
    --sidebar: #2e3350;
    --sidebar-line: #3c4262;
    --tabbar: #0b79c9;
    --tab-active: #262b44;
    --table-head: #1889da;
    --button: #0b79c9;
    --content: #f4f4f4;
    --line: #e3e5ea;
    --row-alt: #f6f7f9;
    --sector-tint: #e6f1fb;
  }
  * { box-sizing: border-box; margin: 0; padding: 0; }
  html, body { width: 1200px; height: 2280px; overflow: hidden; }
  body {
    background: var(--stage);
    font-family: "Poppins", sans-serif;
    color: var(--text);
    display: flex;
    flex-direction: column;
    align-items: center;
    justify-content: center;
    gap: 150px;
  }

  .screen {
    width: 1120px;
    height: 824px;
    background: var(--content);
    display: grid;
    grid-template-columns: 134px 1fr;
    grid-template-rows: 86px 41px 1fr;
    position: relative;
  }

  /* header */
  .topbar {
    grid-column: 1 / 3;
    background: var(--white);
    display: flex;
    align-items: center;
    padding: 0 18px;
  }
  .brand {
    font-weight: 800;
    font-size: 31px;
    color: var(--ink);
    letter-spacing: -0.5px;
  }
  .search {
    margin-left: auto;
    width: 184px;
    height: 23px;
    border: 1px solid var(--line);
    border-radius: 12px;
    display: flex;
    align-items: center;
    justify-content: space-between;
    padding: 0 10px;
    font-size: 8px;
    color: var(--muted);
  }
  .tools { display: flex; gap: 8px; margin-left: 30px; }
  .tool {
    width: 23px; height: 23px;
    border: 1px solid #c5c9d2;
    border-radius: 50%;
    display: flex; align-items: center; justify-content: center;
  }
  .user { display: flex; align-items: center; margin-left: 20px; gap: 8px; }
  .avatar {
    width: 25px; height: 25px; border-radius: 50%;
    background: linear-gradient(135deg, #c9ced8, #55607a);
  }
  .greeting { font-size: 8px; line-height: 12px; color: var(--ink); }
  .greeting strong { font-weight: 500; display: block; }
  .caret { margin-left: 12px; width: 0; height: 0; border-left: 4px solid transparent; border-right: 4px solid transparent; border-top: 5px solid var(--ink); }

  /* sidebar */
  .sidebar {
    grid-row: 2 / 4;
    background: var(--sidebar);
  }
  .nav-item {
    height: 43px;
    display: flex;
    align-items: center;
    gap: 12px;
    padding-left: 13px;
    color: var(--white);
    font-size: 12px;
    font-weight: 500;
    border-bottom: 1px solid var(--sidebar-line);
  }
  .nav-item svg { width: 16px; height: 16px; fill: var(--white); }

  /* tabs */
  .tabs {
    background: var(--tabbar);
    display: flex;
    align-items: stretch;
  }
  .tab {
    color: var(--white);
    font-size: 14px;
    font-weight: 500;
    display: flex; align-items: center;
    padding: 0 17px;
  }
  .tab.active { background: var(--tab-active); font-weight: 600; padding: 0 19px; }

  /* main */
  .main { position: relative; padding: 54px 38px 0 35px; }
  .card {
    background: var(--white);
    border: 1px solid var(--line);
    height: 500px;
    padding: 40px 33px 0 37px;
  }
  .filters { display: flex; align-items: flex-end; gap: 17px; }
  .field label {
    display: block;
    font-size: 11.5px;
    font-weight: 500;
    color: var(--ink);
    margin-bottom: 14px;
    word-spacing: 3px;
  }
  .field .input {
    height: 33px;
    border: 1px solid var(--line);
    font-size: 10px;
    color: var(--ink);
    display: flex; align-items: center;
    padding-left: 12px;
  }
  .export {
    height: 32px;
    background: var(--button);
    color: var(--white);
    font-size: 11.5px;
    font-weight: 500;
    display: inline-flex; align-items: center; gap: 6px;
    padding: 0 18px;
  }
  .export svg { width: 11px; height: 11px; fill: var(--white); }

  table { border-collapse: collapse; width: 100%; font-size: 10px; color: var(--text); }
  thead th {
    background: var(--table-head);
    color: var(--white);
    font-weight: 600;
    font-size: 10.5px;
    height: 36px;
    text-align: center;
  }
  tbody td {
    text-align: center;
    vertical-align: top;
    border-right: 1px solid var(--line);
    border-bottom: 1px solid var(--line);
  }
  tbody td:first-child { border-left: 1px solid var(--line); }
  tbody tr:nth-child(even) td { background: var(--row-alt); }

  .footer {
    position: absolute; left: 0; right: 0; top: 593px;
    text-align: center;
  }
  .footer p { font-size: 12px; color: var(--ink); }
  .social { display: flex; justify-content: center; gap: 4px; margin-top: 22px; }
  .social span { width: 19px; height: 19px; border: 1px solid var(--ink); border-radius: 50%; }

  /* screen-specific */
  .quality .field { width: 268px; }
  .quality table { margin-top: 35px; }
  .quality tbody td { padding: 10px 4px 0; height: 50px; line-height: 15px; }

  .factors .filters { gap: 16px; }
  .factors .field { width: 267px; }
  .factors .action { text-align: center; margin-top: 24px; }
  .factors table { margin-top: 26px; }
  .factors tbody td { vertical-align: middle; height: 35.5px; }
  .factors tbody td.sector { background: var(--sector-tint) !important; }
</style>
</head>
<body>

<!-- Quality screen -->
<section class="screen quality">
  <header class="topbar">
    <div class="brand">Pellworth</div>
    <div class="search">Search...
      <svg width="9" height="9" viewBox="0 0 10 10"><circle cx="4" cy="4" r="3" fill="none" stroke="#9aa0ad" stroke-width="1.2"/><line x1="6.3" y1="6.3" x2="9" y2="9" stroke="#9aa0ad" stroke-width="1.2"/></svg>
    </div>
    <div class="tools">
      <span class="tool"><svg width="11" height="11" viewBox="0 0 12 12"><rect x="1.5" y="2" width="9" height="6" rx="1" fill="none" stroke="#9aa0ad"/><path d="M4 8 L4 10.5 L6.5 8" fill="none" stroke="#9aa0ad"/></svg></span>
      <span class="tool"><svg width="11" height="11" viewBox="0 0 12 12"><path d="M3 11 V2 H9 L7.5 4.5 L9 7 H3" fill="none" stroke="#9aa0ad"/></svg></span>
      <span class="tool"><svg width="11" height="11" viewBox="0 0 12 12"><circle cx="6" cy="6" r="2" fill="none" stroke="#9aa0ad"/><circle cx="6" cy="6" r="4.5" fill="none" stroke="#9aa0ad" stroke-dasharray="2 1.2"/></svg></span>
    </div>
    <div class="user">
      <div class="avatar" role="img" aria-label="User profile photo"></div>
      <div class="greeting">Welcome,<strong>Mara Lindqvist!</strong></div>
      <span class="caret"></span>
    </div>
  </header>

  <nav class="sidebar">
    <div class="nav-item"><svg viewBox="0 0 16 16"><path d="M15 1 L1 7 L6 9 L7 14 L9.5 10.5 L13 13 Z"/></svg>MODELS</div>
    <div class="nav-item"><svg viewBox="0 0 16 16"><circle cx="6" cy="9" r="4"/><circle cx="12" cy="4" r="3"/><circle cx="6" cy="9" r="1.5" fill="#2e3350"/><circle cx="12" cy="4" r="1" fill="#2e3350"/></svg>SENSITIVITIES</div>
    <div class="nav-item"><svg viewBox="0 0 16 16"><path d="M8 14 L2 8 A3.3 3.3 0 0 1 8 3.5 A3.3 3.3 0 0 1 14 8 Z" fill="none" stroke="#fff" stroke-width="1.6"/></svg>FAVOURITES</div>
  </nav>

  <div class="tabs">
    <span class="tab active">QBOSS</span>
    <span class="tab">250D</span>
    <span class="tab">83D</span>
    <span class="tab">42D</span>
  </div>

  <main class="main">
    <div class="card">
      <div class="filters">
        <div class="field"><label>QUALITY &nbsp;THRESHOLD:</label><div class="input">-10</div></div>
        <div class="field"><label>ABS. SIZE &nbsp;THERSHOLD:</label><div class="input">-10</div></div>
        <span class="export"><svg viewBox="0 0 12 12"><path d="M1 1 H6 V4 H9 V1 H6 M1 1 V11 H8 V7 H11 L9 5 V9 L11 7" /></svg>EXPORT</span>
      </div>
      <table>
        <thead>
          <tr><th>ID</th><th>SECTOR</th><th>TIME</th><th>QUALITY</th><th>STAT 1</th><th>STAT 2</th><th>STAT 3</th><th>STAT 4</th><th>STAT 5</th><th>STAT 6</th><th>STAT 7</th><th>STAT 8</th></tr>
        </thead>
        <tbody>
          <tr><td>Model 1</td><td>Materials</td><td>2019-07-03<br>12:15:00.000</td><td>30.2288</td><td>2.01574</td><td>23.305</td><td>-0.149368</td><td>22.3054</td><td>4.63714</td><td>0.945706</td><td>2.81949</td><td>2.60858</td></tr>
          <tr><td>Model 2</td><td>industrials</td><td>2019-07-03<br>12:15:00.000</td><td>32.8694</td><td>0.87307</td><td>32.185</td><td>-0.0336927</td><td>33.9911</td><td>11.5693</td><td>-0.472968</td><td>-0.830458</td><td>6.80646</td></tr>
          <tr><td>Model 3</td><td>Consumer<br>Discretionary</td><td>2019-07-03<br>12:15:00.000</td><td>30.2288</td><td>-0.569222</td><td>159.814</td><td>0.0252328</td><td>172.616</td><td>10.2875</td><td>-0.750396</td><td>-0.385309</td><td>4.69146</td></tr>
          <tr><td>Model 4</td><td>Information<br>Technology</td><td>2019-07-03<br>12:15:00.000</td><td>45.6856</td><td>0.412148</td><td>202.488</td><td>0.00849232</td><td>205.834</td><td>11.9094</td><td>-0.137913</td><td>0.449595</td><td>3.85106</td></tr>
          <tr><td>Model 5</td><td>Information<br>Technology</td><td>2019-07-03<br>12:15:00.000</td><td>75.7733</td><td>7.06728</td><td>188.605</td><td>0.016913</td><td>181.665</td><td>3.82241</td><td>0.981019</td><td>1.29847</td><td>3.34927</td></tr>
        </tbody>
      </table>
    </div>
    <footer class="footer">
      <p>©2019 Pellworth, All Rights Reserved.</p>
      <div class="social"><span></span><span></span><span></span><span></span><span></span></div>
    </footer>
  </main>
</section>

<!-- Factors screen -->
<section class="screen factors">
  <header class="topbar">
    <div class="brand">Pellworth</div>
    <div class="search">Search...
      <svg width="9" height="9" viewBox="0 0 10 10"><circle cx="4" cy="4" r="3" fill="none" stroke="#9aa0ad" stroke-width="1.2"/><line x1="6.3" y1="6.3" x2="9" y2="9" stroke="#9aa0ad" stroke-width="1.2"/></svg>
    </div>
    <div class="tools">
      <span class="tool"><svg width="11" height="11" viewBox="0 0 12 12"><rect x="1.5" y="2" width="9" height="6" rx="1" fill="none" stroke="#9aa0ad"/><path d="M4 8 L4 10.5 L6.5 8" fill="none" stroke="#9aa0ad"/></svg></span>
      <span class="tool"><svg width="11" height="11" viewBox="0 0 12 12"><path d="M3 11 V2 H9 L7.5 4.5 L9 7 H3" fill="none" stroke="#9aa0ad"/></svg></span>
      <span class="tool"><svg width="11" height="11" viewBox="0 0 12 12"><circle cx="6" cy="6" r="2" fill="none" stroke="#9aa0ad"/><circle cx="6" cy="6" r="4.5" fill="none" stroke="#9aa0ad" stroke-dasharray="2 1.2"/></svg></span>
    </div>
    <div class="user">
      <div class="avatar" role="img" aria-label="User profile photo"></div>
      <div class="greeting">Welcome,<strong>Mara Lindqvist!</strong></div>
      <span class="caret"></span>
    </div>
  </header>

  <nav class="sidebar">
    <div class="nav-item"><svg viewBox="0 0 16 16"><path d="M15 1 L1 7 L6 9 L7 14 L9.5 10.5 L13 13 Z"/></svg>MODELS</div>
    <div class="nav-item"><svg viewBox="0 0 16 16"><circle cx="6" cy="9" r="4"/><circle cx="12" cy="4" r="3"/><circle cx="6" cy="9" r="1.5" fill="#2e3350"/><circle cx="12" cy="4" r="1" fill="#2e3350"/></svg>SENSITIVITIES</div>
    <div class="nav-item"><svg viewBox="0 0 16 16"><path d="M8 14 L2 8 A3.3 3.3 0 0 1 8 3.5 A3.3 3.3 0 0 1 14 8 Z" fill="none" stroke="#fff" stroke-width="1.6"/></svg>FAVOURITES</div>
  </nav>

  <div class="tabs">
    <span class="tab active">FACTORS</span>
    <span class="tab">250D</span>
    <span class="tab">83D</span>
    <span class="tab">42D</span>
  </div>

  <main class="main">
    <div class="card">
      <div class="filters">
        <div class="field"><label>STAR 1 THRESHOLD :</label><div class="input">-10</div></div>
        <div class="field"><label>STAR 2 THRESHOLD :</label><div class="input">-10</div></div>
        <div class="field"><label>STAR 3 THRESHOLD :</label><div class="input">-10</div></div>
      </div>
      <div class="action">
        <span class="export"><svg viewBox="0 0 12 12"><path d="M1 1 H6 V4 H9 V1 H6 M1 1 V11 H8 V7 H11 L9 5 V9 L11 7" /></svg>EXPORT</span>
      </div>
      <table>
        <thead>
          <tr><th>FACTOR</th><th>ID</th><th>SECTOR</th><th>STAT 1</th><th>STAT 2</th><th>STAT 3</th><th>STAT 4</th><th>STAT 5</th><th>STAT 6</th></tr>
        </thead>
        <tbody>
          <tr><td>Factor 1</td><td>Model 1</td><td class="sector">Materials</td><td>-1.4</td><td>0.1</td><td>-3.1</td><td>0.7</td><td>30.2</td><td>0.9</td></tr>
          <tr><td>Factor 2</td><td>Model 1</td><td class="sector">Materials</td><td>2.8</td><td>0.1</td><td>6.1</td><td>100</td><td>30.2</td><td>0.9</td></tr>
          <tr><td>Factor 3</td><td>Model 1</td><td class="sector">Materials</td><td>-3.7</td><td>2.7</td><td>-7.2</td><td>100</td><td>30.2</td><td>0.9</td></tr>
          <tr><td>Factor 1</td><td>Model 2</td><td class="sector">Materials</td><td>2.8</td><td>0.2</td><td>2.7</td><td>0.5</td><td>30.9</td><td>-0.5</td></tr>
          <tr><td>Factor 2</td><td>Factor 2</td><td class="sector">Materials</td><td>0.8</td><td>0.3</td><td>2.5</td><td>0.5</td><td>30.9</td><td>-0.5</td></tr>
          <tr><td>Factor 1</td><td>Factor 1</td><td class="sector">Materials</td><td>2.8</td><td>0.3</td><td>2.5</td><td>0.5</td><td>30.9</td><td>-0.5</td></tr>
        </tbody>
      </table>
    </div>
    <footer class="footer">
      <p>©2019 Pellworth, All Rights Reserved.</p>
      <div class="social"><span></span><span></span><span></span><span></span><span></span></div>
    </footer>
  </main>
</section>

</body>
</html>
```